New business card/stationary for a consulting company

I am looking for a clean and very professional looking business card for my consulting company as well as corresponding stationary. I am uploading our logo. I like simple and powerful for the feel. No graphics but I am open on everything else. Below is my contact information but would like the final to be in a version I can add my employees information into and print. Thank you.

Daniel Whitcombe
dan@ferncliffadvisory.com
2870 North 9th Avenue, Summit Floor, Elm Ridge, Illinois 60531
www.ferncliffadvisory.com

Industry/Entity Type

Consulting

Contact Information for Business Card

Daniel Whitcombe
dan@ferncliffadvisory.com
www.ferncliffadvisory.com

Font styles to use
Serif
Sans Serif

Requirements
Must have
• Our logo and the business card details.
Nice to have
• our website www.ferncliffadvisory.com

```html
<!DOCTYPE html>
<html lang="en">
<head>
<meta charset="utf-8">
<title>Ferncliff Advisory – Business Card</title>
<link href="https://fonts.googleapis.com/css2?family=Montserrat:wght@400&family=Open+Sans:wght@400;700&display=swap" rel="stylesheet">
<style>
  :root {
    --navy: #0c0c6b;
    --navy-deep: #080850;
    --paper: #f4f4f4;
    --paper-shade: #e2e2e2;
    --ink-light: #e8e8f2;
    --stage: #d9d9dc;
  }
  * { margin: 0; padding: 0; box-sizing: border-box; }
  html, body { width: 1200px; height: 904px; overflow: hidden; }
  body {
    background: var(--stage);
    font-family: "Open Sans", sans-serif;
    position: relative;
  }
  .card {
    position: absolute;
    left: 290px;
    width: 620px;
    height: 354px;
    overflow: hidden;
    box-shadow: 0 6px 18px rgba(0,0,0,.25);
  }
  /* Back side */
  .card-back {
    top: 56px;
    background: linear-gradient(160deg, var(--navy) 0%, var(--navy-deep) 100%);
    display: flex;
    align-items: center;
    justify-content: center;
  }
  .back-brand {
    display: flex;
    align-items: center;
    gap: 12px;
    font-family: "Montserrat", sans-serif;
    font-size: 22px;
    letter-spacing: 2px;
    text-transform: uppercase;
    color: #b9b9d8;
  }
  .brand-square {
    width: 14px; height: 14px;
    background: currentColor;
  }
  /* Front side */
  .card-front {
    top: 450px;
    background: var(--navy);
  }
  .front-top {
    position: absolute;
    left: 0; top: 0; right: 0;
    height: 178px;
    background: linear-gradient(90deg, var(--paper-shade) 0%, var(--paper) 45%, #fbfbfb 100%);
    display: flex;
    flex-direction: column;
    align-items: center;
    justify-content: center;
    gap: 14px;
  }
  .front-brand {
    display: flex;
    align-items: center;
    gap: 12px;
    font-family: "Montserrat", sans-serif;
    font-size: 24px;
    letter-spacing: 1.5px;
    text-transform: uppercase;
    color: var(--navy);
  }
  .front-rule {
    position: absolute;
    left: 0; right: 0;
    top: 184px;
    height: 4px;
    background: var(--paper);
  }
  .front-rule-top {
    position: absolute;
    left: 0; right: 0;
    top: 172px;
    height: 6px;
    background: var(--navy);
  }
  .front-bottom {
    position: absolute;
    left: 0; right: 0; top: 188px; bottom: 0;
    display: flex;
    align-items: center;
  }
  .holder-name {
    width: 290px;
    text-align: right;
    padding-right: 26px;
    font-weight: 700;
    font-size: 19px;
    color: var(--ink-light);
  }
  .divider {
    width: 1px;
    height: 118px;
    background: var(--ink-light);
    opacity: .8;
  }
  .contact {
    padding-left: 22px;
    font-size: 13.5px;
    line-height: 1.45;
    color: var(--ink-light);
    list-style: none;
  }
  .contact li { display: flex; align-items: center; gap: 8px; }
  .contact svg { width: 14px; height: 14px; flex: none; }
</style>
</head>
<body>
  <section class="card card-back" aria-label="Card back">
    <div class="back-brand"><span class="brand-square"></span>Ferncliff Advisory</div>
  </section>

  <section class="card card-front" aria-label="Card front">
    <div class="front-top">
      <div class="front-brand"><span class="brand-square"></span>Ferncliff Advisory</div>
    </div>
    <div class="front-rule-top"></div>
    <div class="front-rule"></div>
    <div class="front-bottom">
      <p class="holder-name">Daniel Whitcombe</p>
      <div class="divider"></div>
      <ul class="contact">
        <li>2870 North 9th Avenue</li>
        <li>Summit Floor, Elm Ridge</li>
        <li>Illinois 60531</li>
        <li>
          <svg viewBox="0 0 14 14" aria-hidden="true"><circle cx="7" cy="7" r="7" fill="#e8e8f2"/><rect x="3" y="4.5" width="8" height="5.5" fill="none" stroke="#0c0c6b" stroke-width="1"/><path d="M3 4.5 L7 7.8 L11 4.5" fill="none" stroke="#0c0c6b" stroke-width="1"/></svg>
          dan@ferncliffadvisory.com
        </li>
        <li>
          <svg viewBox="0 0 14 14" aria-hidden="true"><circle cx="7" cy="7" r="7" fill="#e8e8f2"/><circle cx="7" cy="7" r="4.2" fill="none" stroke="#0c0c6b" stroke-width="1"/><ellipse cx="7" cy="7" rx="1.8" ry="4.2" fill="none" stroke="#0c0c6b" stroke-width="1"/><line x1="2.8" y1="7" x2="11.2" y2="7" stroke="#0c0c6b" stroke-width="1"/></svg>
          www.ferncliffadvisory.com
        </li>
      </ul>
    </div>
  </section>
</body>
</html>
```